Luxury sell sheet flyer Design

We need two luxury/premium looking sales flyer - one for luxury and one for travel-

Please find flyers from last year (2015) attached. Please copy the pictures and the look and feel (and colors), and use the content form the 2016 documents.

These flyers will be used for corporate subscription sales and targetted at CMOs and Marketing heads. As such they should convey a very premium look and feel.

Please provide in format that we can make text edits in later.

USA, UK, Asia

Travel

Serif

• Good copyright free pictures, no clip art, that show a very premium look and feel for a corporate flyer
• clean feel, not cluttered
• clip art

```html
<!DOCTYPE html>
<html lang="en">
<head>
<meta charset="utf-8">
<title>2016 Prime Horizons Travel Subscription Service</title>
<link rel="stylesheet" href="https://fonts.googleapis.com/css2?family=Montserrat:wght@500;600&family=Tinos:ital,wght@0,400;0,700;1,400;1,700&family=Arimo:wght@400;700&display=swap">
<style>
:root{
  --navy:#1d3e63;
  --blue:#2a86c0;
  --sky:#cfe6f6;
  --sky-deep:#a9d2ee;
  --tan:#d8c6b0;
  --ink:#1a1a1a;
  --plus:#9a9a9a;
  --premium:#d49a6a;
  --prestige:#c8a24a;
  --bg:#e9ebee;
}
*{margin:0;padding:0;box-sizing:border-box}
html,body{width:1200px;height:869px;overflow:hidden;background:var(--bg)}
body{position:relative;font-family:"Tinos",serif;color:var(--ink)}
.page{position:absolute;top:78px;width:527px;height:680px;overflow:hidden;box-shadow:0 6px 18px rgba(0,0,0,.18)}
.page--front{left:55px;background:#fff}
.page--back{left:626px;background:linear-gradient(160deg,#ffffff 0%,#eaf4fb 35%,#cfe6f6 75%,#bcdcf2 100%)}
.hero{position:absolute;left:0;top:0;width:527px;height:334px;background:linear-gradient(120deg,#d9ecf8 0%,#b6d9f1 45%,#6f8ea8 80%,#3a4a5a 100%)}
.hero-title{position:absolute;left:42px;top:46px;font-family:"Montserrat",sans-serif;font-weight:600;color:var(--navy);font-size:30px;line-height:35px}
.band{position:absolute;left:0;height:8px;width:100%;background:var(--tan)}
.front-lower{position:absolute;left:0;top:342px;width:527px;height:338px;background:linear-gradient(180deg,#fff 0%,#f3f8fc 50%,#cfe6f6 100%)}
.intro{position:absolute;left:27px;top:372px;width:266px;font-size:9.4px;line-height:14px}
.dropcap{float:left;width:22px;height:22px;margin:2px 3px 0 0;background:var(--blue);color:#fff;font-size:22px;line-height:22px;text-align:center}
.offer{position:absolute;left:304px;top:365px;width:202px;height:200px;border-radius:8px;background:linear-gradient(160deg,#2f9ad3,#1b6fa8);color:#fff;font-family:"Arimo",sans-serif;padding:14px 12px}
.offer h3{font-size:10.5px;font-weight:700;line-height:12.5px;margin-bottom:9px}
.offer ol{padding-left:22px;font-size:10.2px;line-height:12.5px}
.offer li{margin-bottom:7px}
.prices{position:absolute;left:304px;top:572px;width:202px;border-collapse:collapse;font-family:"Arimo",sans-serif;font-size:10px}
.prices td,.prices th{height:17px;padding:0 4px;border-bottom:1px solid #fff;white-space:nowrap}
.prices th{background:#111;color:#fff;font-weight:400;text-align:left}
.prices th.tier{font-size:10px;text-align:center}
.prices th:first-child{font-style:italic;font-size:8px}
.prices td.name{color:#fff;font-weight:700;font-size:9.4px;width:136px}
.prices td.cost{background:#f1ece4;font-style:italic;text-align:center}
.plus{background:var(--plus)} .premium{background:var(--premium)} .prestige{background:var(--prestige)}
.foot{position:absolute;left:27px;right:28px;top:658px;display:flex;align-items:center;gap:8px}
.foot i{flex:1;border-top:3px double #7a8ea3}
.foot span{font-family:"Arimo",sans-serif;font-weight:700;font-size:8.6px;color:var(--navy)}
.back-title{position:absolute;left:23px;top:14px;font-size:12.2px;font-weight:700;color:var(--navy)}
.t7{font-size:7.6px;line-height:10px}
.sub{position:absolute;left:23px;top:34px}
.cat-lead{position:absolute;left:23px;top:54px;font-style:italic;font-weight:700}
.cats{position:absolute;left:23px;top:66px;width:430px;border-collapse:collapse;background:#fff;font-size:7.6px}
.cats td{border:1px solid var(--blue);padding:1px 10px;height:13px;line-height:10px}
.focus{position:absolute;left:23px;top:122px;width:272px}
.focus p{margin-bottom:9px}
.defs-lead{position:absolute;left:308px;top:122px}
.defs{position:absolute;left:304px;top:136px;width:152px;border-collapse:collapse;font-size:6.6px}
.defs th{text-align:left;padding:2px 8px;font-weight:700}
.defs td{background:#fff;border:1px solid var(--sky-deep);padding:0 8px;height:14px}
.defs td:first-child{font-weight:700}
.rule{position:absolute;left:23px;top:268px;width:480px;border-top:1px solid #9ab}
.col{position:absolute;top:276px;font-size:5.9px;line-height:7.4px}
.col--a{left:23px;width:218px}
.col--b{left:250px;width:250px}
.col p{margin-bottom:4px}
.col b{font-weight:700}
.col .head{font-weight:700;text-transform:uppercase}
.twin{display:flex;gap:8px}
.twin ul{list-style:none;flex:1}
.press-lead{position:absolute;left:66px;top:621px;font-family:"Arimo",sans-serif;font-weight:700;font-size:8px;line-height:12px;color:var(--navy)}
.press{position:absolute;left:242px;top:602px;width:258px;height:62px;background:#fff;display:flex;flex-wrap:wrap;align-content:space-around;justify-content:space-around;padding:4px 6px;font-size:6.2px;font-weight:700;color:#333}
.press span{padding:1px 3px}
</style>
</head>
<body>

<section class="page page--front">
  <div class="hero" role="img" aria-label="Smiling businessman in a suit seated in an airport lounge with a tablet and rolling suitcase"></div>
  <h1 class="hero-title">2016<br>Prime Horizons<br>Travel Subscription<br>Service</h1>
  <div class="band" style="top:334px"></div>
  <div class="front-lower"></div>

  <div class="intro">
    <p><span class="dropcap">A</span>ffluent Asian consumers continue to be the leading travellers into 2016, with increasing numbers heading to global travel destinations. These travellers are driving premium travel service and luxury goods consumption across Asia and globally. Brands and marketers need to increasingly monitor the pulse of these discerning consumers to uncover their trends and purchase preferences. At Meridian Research we have exclusive access to engage with this hard to reach customer base through our EliteCircle™ community. A closed door, invitation only community of affluent and HNWI consumers across 20 key markets built through key luxury partnerships.</p>
    <p>To cater to a growing response of requests from travel brands and those marketing to traveling consumers, we at Meridian have designed an annual program – The Meridian Prime Horizons™ a subscription service that provides market and category specific data, updated every six months, aimed at uncovering the trends, consumption patterns, brand preferences, and detailed insights of the Affluent travel consumers in key Asian markets.</p>
  </div>

  <div class="offer">
    <h3>The subscription service comprises of four offerings:</h3>
    <ol>
      <li>Affluent Asian Travel Consumer Reports (semi-annual)</li>
      <li>Semi-annual Roundtables with Senior Executives from the Luxury Travel World</li>
      <li>Custom Tabulations of Data (semi-annual)</li>
      <li>Semi-annual Brainstorming Sessions with Meridian Experts</li>
    </ol>
  </div>

  <table class="prices">
    <tr><th>Subscription Level:</th><th class="tier">Price Tiers</th></tr>
    <tr><td class="name plus">Prime Horizons PLUS</td><td class="cost">USD 19,500</td></tr>
    <tr><td class="name premium">Prime Horizons PREMIUM</td><td class="cost">USD 22,500</td></tr>
    <tr><td class="name prestige">Prime Horizons PRESTIGE</td><td class="cost">USD 26,500</td></tr>
  </table>

  <div class="foot"><i></i><span>2016 Prime Horizons Travel Subscription Service</span></div>
</section>

<section class="page page--back">
  <h2 class="back-title">AFFLUENT ASIAN TRAVEL CONSUMER REPORTS</h2>
  <p class="sub t7">The 2016 subscription includes two reports per market, one released half-way and the other one at the end of the year.</p>
  <p class="cat-lead t7">The following travel and luxury product categories are covered in each market:</p>
  <table class="cats">
    <tr><td>Hotels (49 brands)</td><td>Cruise Lines (21 brands)</td><td>Airlines (50 brands)</td></tr>
    <tr><td>Travel Destinations (44 destinations</td><td>Designer Clothing &amp; Accessories (83 brands)</td><td>Watches (82 brands)</td></tr>
    <tr><td>Jewellery (39 brands)</td><td>Skincare (52 brands)</td><td>Makeup (49 brands)</td></tr>
  </table>

  <div class="focus t7">
    <p>In each market we are focusing on affluent travel consumers (approximately top-20% of the population based on household income) who have travelled internationally in the past 12 months or planning to travel in the next 12 months. We are fielding two waves in 2016, and interviewing a total of n=300 affluent consumers in each market (at least 100 respondents in each market are past-12/next-12-month cruise travellers/intenders).</p>
    <p>Markets included in the study (content is partially trended to last year in all markets)<br><b>• China • India • Singapore • Hong Kong • Malaysia • S. Korea<br>• Taiwan • Japan</b></p>
    <p>Other markets, such as, Indonesia, Thailand, and Australia can be added by request.</p>
  </div>

  <p class="defs-lead t7">Affluent consumer definitions are as follows:</p>
  <table class="defs">
    <tr><th>COUNTRY</th><th>Annual HHI</th></tr>
    <tr><td>China</td><td>CNY 200,000+</td></tr>
    <tr><td>India</td><td>INR 12,00,000+</td></tr>
    <tr><td>Singapore</td><td>SGD 110,000+</td></tr>
    <tr><td>Hong Kong</td><td>HKD 720,000+</td></tr>
    <tr><td>Malaysia</td><td>MYR 120,000+</td></tr>
    <tr><td>South Korea</td><td>KRW 78 million +</td></tr>
    <tr><td>Taiwan</td><td>NT$ 960,000+</td></tr>
    <tr><td>Japan</td><td>JPY 10,000,000+</td></tr>
  </table>

  <div class="rule"></div>

  <div class="col col--a">
    <p><b>Key analytics in the reports include:</b><br><b>Luxury Brand Index</b> – A tool to help brands understand how well they are meeting the expectation of their potential travel customers in relation to their competitors in different markets. The index is derived from the importance of different dimensions of luxury on category purchase intent and brands' ratings on the same dimensions.</p>
    <p><b>Luxury Brand Media Reach</b> – Gives the brands vital information on how well they are being noticed by travellers in the most relevant media touchpoints. This is calculated based on the importance of different media touchpoints for affecting category purchasing and recall of brand recall in the relevant touchpoints.</p>
    <p><b>Luxury Consumer Segmentation</b> - We have identified unique key luxury consumer types that are different in their motivations and purchase behaviour towards luxury brands. This segmentation will help brands understand their key consumer types in each market.</p>
    <p><b>Affluent Luxury Consumer Insights</b> – We will have numerous analyses to help you understand and profile affluent Asian travel consumers in each market, looking at their purchase behaviour, media influences, psychographics, and demographics. Many of the analyses will be trended to understand shifts in consumer preferences. Key topics for the analyses include:</p>
    <div class="twin">
      <ul>
        <li>• Purchase Triggers</li><li>• Most recent trip</li><li>&nbsp;&nbsp;Influences</li><li>&nbsp;&nbsp;Loyalty programs</li><li>&nbsp;&nbsp;Advertising</li><li>&nbsp;&nbsp;Recommendations</li><li>&nbsp;&nbsp;Editorials</li><li>&nbsp;&nbsp;Travel agents</li><li>&nbsp;&nbsp;How travel was booked</li><li>&nbsp;&nbsp;Class of travel</li><li>&nbsp;&nbsp;Destination type</li><li>&nbsp;&nbsp;Activities</li>
      </ul>
      <ul>
        <li>• What looking forward to from next trip?</li><li>• Travel and Luxury Categories and Brands Intended to Purchase</li><li>• Spend and Share of Wallet for Different Luxury Categories</li><li>• Media Touchpoints Relevant to Each Category</li><li>• Psychographics around Luxury Travel Purchase Behaviour</li><li>• Hobbies and Interests</li><li>• Travel preferences</li><li>• Affluent Travel Consumer Profiles</li>
      </ul>
    </div>
  </div>

  <div class="col col--b">
    <p><span class="head">Semi-annual roundtables</span> (with Senior Executives from the Luxury Travel World)<br>These are private, invitation-only, informal lunch and evening sessions held quarterly at central premium locations in Hong Kong and Singapore. During these sessions we will share latest findings on affluent Asian travel consumers and moderate a discussion on topical themes among travel leaders (including executives from luxury travel brands and travel though leaders).</p>
    <p><span class="head">Custom tabulations of data</span><br>We will provide a set of tabulations of the data for all basic graphs included in the report with custom cuts (up to 20 banner points), e.g., you target consumer age groups, or consumers who are planning a purchase from your competitive brand set.</p>
    <p><span class="head">Semi-annual brainstorming sessions</span> (with Meridian Experts)<br>We will facilitate two brainstorming sessions (timed after the release of each of the Affluent Consumer and Luxury Brand Reports). In these two-hour sessions we will walk you through the findings from the latest data release, and together with you look at implications the findings have on your specific brand(s), and brainstorm on how your brand can best make us of the findings. These sessions can be held in our or your premises in Singapore or Hong Kong.<br>2016 Prime Horizons Travel Subscription Service has three optional service tiers:</p>
    <p><b>Prime Horizons Plus</b><br>&nbsp;&nbsp;2 Affluent Asian Travel Consumer Reports<br><b>Prime Horizons Premium</b><br>&nbsp;&nbsp;2 Affluent Asian Travel Consumer Reports<br>&nbsp;&nbsp;1 Invitation to Semi-annual Travel Leader Roundtables<br>&nbsp;&nbsp;1 Set of Custom Tabulations of Data (per market)<br><b>Prime Horizons Prestige</b><br>&nbsp;&nbsp;2 Affluent Asian Travel Consumer Reports<br>&nbsp;&nbsp;2 Invitations to Semi-annual Travel Leader Roundtables<br>&nbsp;&nbsp;2 Sets of Custom Tabulations of Data (per market)<br>&nbsp;&nbsp;2 Semi-annual Brainstorming Sessions (per market) or speaking engagements.<br>&nbsp;&nbsp;(We have spoken at key events with Grand Voyage Forum, Prestige Ledger, Wayfarer Summit, Global Herald (Travel &amp; Luxury Summit), and Opulence Circle)<br>&nbsp;&nbsp;Pricing for each category is as follows:</p>
  </div>

  <p class="press-lead">Our research has been featured<br>in international media, such as:</p>
  <div class="press">
    <span>Prestige Ledger</span><span>Global Herald</span><span>Harbor Broadcast</span><span>Pacific One</span>
    <span>Strait Media</span><span>Lantern</span><span>Adline</span><span>Eastern Daily</span>
    <span>Siam Courier</span><span>Ledger Daily</span><span>Market Wire</span>
  </div>

  <div class="band" style="bottom:0"></div>
</section>

</body>
</html>
```